Professional & attention grabbing.

A business card design, front and back. I already have a logo I will attach, but I am open to something new as well.
Things to include:
Name:
Title:
Phone:
Email:
Wanting something that is professional but attention grabbing.
Also we do a lot of work using drones on natural gas pipelines (leading the future)if you want to include any of that. I'm open to ideas.
Target Market(s)
Natural gas transmission industry / greenhouse gas mitigation industry
Industry/Entity Type
Business
Colors
Designer to choose colors to be used in the design.
Look and feel
Each slider illustrates characteristics of the customer's brand and the style your logo design should communicate.

```html
<!DOCTYPE html>
<html lang="en">
<head>
<meta charset="utf-8">
<title>Halden Survey Co – Business Card</title>
<link rel="stylesheet" href="https://fonts.googleapis.com/css2?family=Montserrat:wght@700&family=Roboto:wght@400;500&display=swap">
<style>
  :root {
    --page-bg: #d9d4cd;
    --card-light: #ebe8e4;
    --card-light-edge: #dcd8d3;
    --panel-dark: #2f3033;
    --panel-dark-deep: #242528;
    --brand-red: #b3232b;
    --text-dark: #333336;
    --text-white: #f4f4f4;
  }
  html, body {
    margin: 0;
    padding: 0;
    width: 1200px;
    height: 1010px;
    overflow: hidden;
    background: var(--page-bg);
  }
  .canvas {
    position: relative;
    width: 1200px;
    height: 1010px;
  }
  .business-card {
    position: absolute;
    left: 100px;
    top: 215px;
    width: 1000px;
    height: 580px;
    box-shadow: 0 12px 40px rgba(0,0,0,0.18);
  }
  .business-card svg { display: block; }
  .card-details {
    position: absolute;
    left: 512px;
    top: 182px;
    font-family: "Roboto", Arial, sans-serif;
    color: var(--text-dark);
  }
  .holder-name {
    margin: 0;
    font-family: "Montserrat", Arial, sans-serif;
    font-weight: 700;
    font-size: 34px;
    letter-spacing: 1.5px;
    color: var(--brand-red);
    line-height: 1;
  }
  .holder-title {
    margin: 12px 0 0;
    font-size: 21px;
    font-weight: 400;
  }
  .contact-list {
    list-style: none;
    margin: 42px 0 0;
    padding: 0;
  }
  .contact-item {
    display: flex;
    align-items: center;
    gap: 16px;
    font-size: 22px;
    height: 33px;
  }
  .contact-icon { width: 20px; height: 20px; flex: none; }
  .brand-name {
    position: absolute;
    left: 40px;
    top: 272px;
    width: 320px;
    display: flex;
    align-items: center;
    justify-content: center;
    gap: 12px;
    white-space: nowrap;
    font-family: "Roboto", Arial, sans-serif;
    font-weight: 500;
    font-size: 28px;
    letter-spacing: 0.5px;
    color: var(--text-white);
  }
  .brand-dot {
    width: 14px;
    height: 14px;
    border-radius: 50%;
    background: var(--text-white);
  }
</style>
</head>
<body>
<main class="canvas">
  <section class="business-card">
    <svg width="1000" height="580" viewBox="0 0 1000 580" aria-hidden="true">
      <defs>
        <linearGradient id="frostFill" x1="0" y1="0" x2="1" y2="1">
          <stop offset="0" stop-color="var(--card-light)"/>
          <stop offset="1" stop-color="var(--card-light-edge)"/>
        </linearGradient>
        <linearGradient id="panelFill" x1="0" y1="0" x2="0" y2="1">
          <stop offset="0" stop-color="var(--panel-dark)"/>
          <stop offset="1" stop-color="var(--panel-dark-deep)"/>
        </linearGradient>
      </defs>
      <rect class="card-surface" width="1000" height="580" fill="url(#frostFill)"/>
      <path class="panel-accent" d="M0 0 H368 C395 80 430 180 425 300 C420 420 360 510 330 580 H0 Z" fill="var(--brand-red)"/>
      <path class="panel-dark" d="M0 0 H362 C388 80 420 180 414 300 C408 410 348 505 316 580 H0 Z" fill="url(#panelFill)"/>
      <rect width="1000" height="580" fill="none" stroke="rgba(255,255,255,0.6)" stroke-width="1.5"/>
    </svg>

    <div class="brand-name"><span class="brand-dot"></span>Halden Survey Co</div>

    <div class="card-details">
      <h1 class="holder-name">ALEX CARTER</h1>
      <p class="holder-title">Managing Director</p>
      <ul class="contact-list">
        <li class="contact-item">
          <svg class="contact-icon" viewBox="0 0 20 20" aria-hidden="true"><path d="M2 7 C2 4 6 3 10 3 C14 3 18 4 18 7 L14.5 8.5 L13.5 6.5 H6.5 L5.5 8.5 Z M5 10 H15 L16.5 17 H3.5 Z" fill="var(--brand-red)"/><circle cx="10" cy="13.3" r="1.8" fill="var(--card-light)"/></svg>
          <span>1300 418 502</span>
        </li>
        <li class="contact-item">
          <svg class="contact-icon" viewBox="0 0 20 20" aria-hidden="true"><circle cx="10" cy="10" r="8" fill="var(--brand-red)"/><g fill="none" stroke="var(--card-light)" stroke-width="1.2"><ellipse cx="10" cy="10" rx="3.5" ry="8"/><line x1="2" y1="10" x2="18" y2="10"/><line x1="10" y1="2" x2="10" y2="18"/></g></svg>
          <span>www.haldensurvey.com</span>
        </li>
        <li class="contact-item">
          <svg class="contact-icon" viewBox="0 0 20 20" aria-hidden="true"><rect x="1" y="4" width="18" height="12" fill="var(--brand-red)"/><path d="M1 4 L10 11 L19 4" fill="none" stroke="var(--card-light)" stroke-width="1.3"/></svg>
          <span>alex.carter@haldensurvey.com</span>
        </li>
      </ul>
    </div>
  </section>
</main>
</body>
</html>
```